Direct to Consumer extended service contract business with a new disruptive business model needs a

We need a customized wordpress design for a company called 'Bright Harbor Assurance'.
We provide an innovative and unique service contract protection program direct to consumers. This program provides monthly coverage for all electronics purchased in the last 4 years and all electronics the consumer purchases in the future for a low monthly fee. The overall design should communicate a sense of legitimacy, ethics, and superior customer service and support (in an industry that has a huge PR issue to overcome).
Electronics is the first product group, other product groups with different price points to launch in the future..

Target Market(s)

All purchasers of electronic goods...all demographics

Industry/Entity Type

Electronics

Font styles to use
Sans Serif

Requirements
Must have
• Customer Testimonials
Industry News
Customer ratings
Blog posts
Call to action messaging
Like the functional elements and design of quillmesa.example (need to be better)
Nice to have
• Like to see video testimonials
Social network "whats trending related to electronics or service contract industry"
Easy way to register products for warranty

```html
<!DOCTYPE html>
<html lang="en">
<head>
<meta charset="utf-8">
<title>Bright Harbor Assurance – Home Page Concepts</title>
<link href="https://fonts.googleapis.com/css2?family=Oswald:wght@500;600&family=Open+Sans:wght@400;600;700&family=Roboto+Condensed:ital,wght@1,700&display=swap" rel="stylesheet">
<style>
:root{
  --bark:#3a2a1c;
  --bark-deep:#2c2017;
  --sand:#d5c4aa;
  --mist:#ecE8e1;
  --orange:#f07c14;
  --orange-deep:#c8470f;
  --ink:#2a2522;
  --grey:#8a8580;
  --paper:#ffffff;
  --star-red:#e0302a;
  --star-blue:#3d84d8;
  --star-green:#6dbb2f;
}
*{box-sizing:border-box;margin:0;padding:0}
html,body{width:1200px;height:1145px;overflow:hidden;background:#fff}
body{font-family:"Open Sans",Arial,sans-serif;color:var(--ink)}
.canvas{position:relative;width:1200px;height:1145px;overflow:hidden;background:#fff}
.site{position:absolute;top:0;width:500px;height:1145px;overflow:hidden;box-shadow:0 0 14px rgba(0,0,0,.18)}
.site--light{left:50px}
.site--dark{left:651px}
.site>section,.site>header,.site>footer{position:absolute;left:0;width:500px}

/* masthead */
.masthead{top:0;height:48px;background:var(--bark)}
.util-tab{position:absolute;right:5px;top:0;width:112px;height:14px;background:var(--orange);border-radius:0 0 3px 3px;font:700 5.5px/14px "Open Sans",sans-serif;color:#fff;display:flex;justify-content:space-around}
.brand{position:absolute;left:40px;top:9px;display:flex;align-items:center;gap:6px}
.brand-mark{width:26px;height:26px;background:var(--sand)}
.brand-name{font:500 11px/12px "Oswald",sans-serif;color:#eadcbc;letter-spacing:.3px;text-transform:uppercase}
.nav{position:absolute;left:222px;top:26px;display:flex;gap:11px;font:700 7.5px/11px "Open Sans",sans-serif;color:#e9dcc6;text-transform:uppercase}
.nav .is-current{color:#fff;border-bottom:2px solid var(--orange)}

/* hero */
.hero{top:48px;height:272px;background:var(--sand)}
.device{position:absolute;left:22px;top:24px;width:233px;height:143px;border-radius:6px;background:linear-gradient(180deg,#2b2b2b 0,#2b2b2b 8%,#eef2f6 9%,#dfe7ee 85%,#b9bcbf 88%,#8d9094 100%)}
.claims{position:absolute;right:39px;top:49px;display:flex;flex-direction:column;align-items:flex-end;gap:3px}
.claims span{background:#1e1712;color:#fff;font:500 14.5px/18px "Oswald",sans-serif;letter-spacing:1.2px;padding:0 4px;text-transform:uppercase}
.quote-btn{position:absolute;right:39px;top:119px;width:185px;height:23px;background:var(--orange);color:#fff;font:500 16px/23px "Oswald",sans-serif;letter-spacing:.8px;text-align:center;text-transform:uppercase}
.features{position:absolute;left:41px;top:188px;width:418px;height:84px;background:var(--paper);display:flex;gap:4px;padding:8px 6px}
.feature{width:133px}
.feature-head{height:28px;background:var(--orange);display:flex;align-items:center;gap:6px;padding:0 6px;color:#fff;font:500 8.5px/9px "Oswald",sans-serif;text-transform:uppercase}
.feature-head svg{flex:none}
.feature ul{list-style:none;margin-top:6px;padding-left:3px;font-size:5.8px;line-height:8.5px;color:#555}
.site--dark .feature-head{background:var(--orange-deep)}

/* section titles */
.section-title{position:absolute;left:0;width:500px;text-align:center;font:italic 700 13px/16px "Roboto Condensed",sans-serif;color:var(--orange)}
.site--dark .section-title{color:#d9541b}
.site--dark .band .section-title{color:#fff}

/* ratings */
.band{background:var(--mist)}
.site--dark .band{background:var(--bark)}
.ratings{top:320px;height:120px}
.ratings .section-title{top:13px}
.arrow{position:absolute;width:0;height:0;border-top:6px solid transparent;border-bottom:6px solid transparent}
.arrow--prev{border-right:6px solid var(--ink)}
.arrow--next{border-left:6px solid var(--ink)}
.site--dark .arrow--prev{border-right-color:#fff}
.site--dark .arrow--next{border-left-color:#fff}
.ratings .arrow{top:67px}
.store{position:absolute;top:51px;display:flex;gap:5px;align-items:flex-start}
.store-dot{width:42px;height:42px;border-radius:50%;flex:none}
.store-name{font-size:11px;line-height:13px;color:var(--ink)}
.store-note{font-size:7.5px;line-height:9px;color:#444}
.stars{font-size:11px;line-height:13px;letter-spacing:1px}
.site--dark .store-name,.site--dark .store-note{color:#fff}

/* cards */
.news{top:440px;height:230px;background:var(--paper)}
.news .section-title{top:16px}
.blog{top:820px;height:208px;background:var(--paper)}
.blog .section-title{top:18px}
.card{position:absolute;width:133px}
.news .card{top:42px;height:126px;border-bottom:1px solid #ddd}
.blog .card{top:49px}
.photo{width:133px;height:98px}
.card h3{font:400 9px/12px "Open Sans",sans-serif;color:var(--ink);margin:2px 0 0 3px}
.card .meta{font:italic 600 5px/6px "Open Sans",sans-serif;color:var(--orange);margin-left:3px}
.card .excerpt{font-size:5.3px;line-height:8px;color:#999;margin:8px 3px 0}

/* testimonials */
.testimonials{top:670px;height:150px}
.testimonials .section-title{top:17px}
.testimonials .arrow{top:80px}
.video{position:absolute;top:47px;width:139px;height:77px;background:linear-gradient(135deg,#0d2f5e 0,#1d4c85 55%,#5b6a7c 100%);display:flex;align-items:center;justify-content:center}

/* footer */
.site-footer{top:1028px;height:102px;background:var(--sand)}
.site--dark .site-footer{background:var(--bark)}
.foot-col{position:absolute;top:16px}
.foot-col h4{font:700 7px/9px "Open Sans",sans-serif;text-transform:uppercase;color:var(--ink);padding-bottom:3px;border-bottom:1px solid #6a5a48}
.site--dark .foot-col h4{color:#fff;border-bottom-color:#cbb89c}
.foot-links{display:flex;gap:28px;margin-top:9px;font-size:6px;line-height:9px;color:var(--ink)}
.foot-links ul{list-style:none}
.site--dark .foot-links,.site--dark .contact-list{color:#fff}
.social-row{position:absolute;right:0;top:-8px;display:flex;gap:3px}
.social-row i{display:block;width:14px;height:14px}
.feed{margin-top:6px;width:128px;height:63px;background:#fff;padding:3px 5px}
.feed-item{display:flex;gap:6px;align-items:center;height:19px}
.feed-item b{width:14px;height:14px;border-radius:50%;background:#d9541b;flex:none}
.feed-item p{font-size:4.3px;line-height:5.5px;color:#333}
.feed-item span{color:var(--orange);display:block}
.contact-list{list-style:none;margin-top:8px;font-size:5.8px;line-height:7.5px;color:var(--ink);font-style:italic}
.contact-list li{display:flex;gap:4px}
.legal{top:1130px;height:15px;background:var(--bark-deep);color:#fff;font:600 6px/15px "Open Sans",sans-serif;text-align:center}
</style>
</head>
<body>
<div class="canvas">

  <!-- light variant -->
  <div class="site site--light">
    <header class="masthead">
      <div class="util-tab"><span>Login</span><span>Support</span><span>Call: 555-010-4477</span></div>
      <div class="brand"><span class="brand-mark"></span><span class="brand-name">Bright Harbor<br>Assurance</span></div>
      <nav class="nav"><span class="is-current">Home</span><span>Plans</span><span>Benefits</span><span>About us</span><span>Blog</span><span>News</span><span>Contact</span></nav>
    </header>

    <section class="hero">
      <div class="device" role="img" aria-label="Laptop showing the quote form and customer ratings screen"></div>
      <div class="claims"><span>Buys your device</span><span>Pay monthly to secure</span><span>Claim/fix your device</span></div>
      <div class="quote-btn">Get free quote</div>
      <div class="features">
        <div class="feature">
          <div class="feature-head"><svg width="18" height="18" viewBox="0 0 18 18"><circle cx="9" cy="9" r="8" fill="#fff"/><text x="9" y="12.5" font-size="10" text-anchor="middle" fill="#f07c14" font-family="Oswald,sans-serif">$</text></svg><span>Purchase in low<br>rates</span></div>
          <ul><li>- 1000 products available online</li><li>- Low as price as compare to market price</li><li>- Easy to purchase any product</li></ul>
        </div>
        <div class="feature">
          <div class="feature-head"><svg width="18" height="18" viewBox="0 0 18 18"><path d="M9 1 L16 4 V9 C16 13 12.5 16 9 17 C5.5 16 2 13 2 9 V4 Z" fill="#fff"/></svg><span>Protect devices<br>by paying monthly</span></div>
          <ul><li>- Pay montly fee</li><li>- Low rates as compare to others</li><li>- Secure your device in advance</li></ul>
        </div>
        <div class="feature">
          <div class="feature-head"><svg width="18" height="18" viewBox="0 0 18 18"><rect x="2" y="3" width="14" height="12" rx="2" fill="none" stroke="#fff" stroke-width="2"/></svg><span>Claim and fix<br>your device</span></div>
          <ul><li>- Claim your money you have paid</li><li>- Fix your broken devices</li><li>- Fast and reliable</li></ul>
        </div>
      </div>
    </section>

    <section class="ratings band">
      <h2 class="section-title">Customer Raiting</h2>
      <span class="arrow arrow--prev" style="left:11px"></span>
      <div class="store" style="left:29px"><span class="store-dot" style="background:#2b2b2b"></span><div><div class="store-name">Orchard Store</div><div class="store-note">some info came here<br>with description.</div><div class="stars" style="color:var(--star-red)">★★★★★</div></div></div>
      <div class="store" style="left:175px"><span class="store-dot" style="background:#3a3a3a"></span><div><div class="store-name">Riverbend Store</div><div class="store-note">some info came here<br>with description.</div><div class="stars" style="color:var(--star-blue)">★★★★★</div></div></div>
      <div class="store" style="left:326px"><span class="store-dot" style="background:#e0312a"></span><div><div class="store-name">Glimmer Store</div><div class="store-note">some info came here<br>with description.</div><div class="stars" style="color:var(--star-green)">★★★★★</div></div></div>
      <span class="arrow arrow--next" style="left:462px"></span>
    </section>

    <section class="news">
      <h2 class="section-title">Industry News</h2>
      <article class="card" style="left:47px"><div class="photo" role="img" aria-label="Shopper browsing laptops in an electronics store" style="background:linear-gradient(135deg,#c9d3dc,#3f5873)"></div><h3>Lorem ipsum nipsum saye</h3><p class="meta">Posted on: Sep 29th, 2014</p><p class="excerpt">Lorem ipsum nipsum saye lorem ipsum nipsum saye. Lorem ipsum saye lorem ipsum nipsum saye.</p></article>
      <article class="card" style="left:184px"><div class="photo" role="img" aria-label="Woman with a touchscreen interface" style="background:linear-gradient(135deg,#dfe6ea,#9aa7b0)"></div><h3>Lorem ipsum nipsum saye</h3><p class="meta">Posted on: Sep 29th, 2014</p><p class="excerpt">Lorem ipsum nipsum saye lorem ipsum nipsum saye. Lorem ipsum saye lorem ipsum nipsum saye.</p></article>
      <article class="card" style="left:320px"><div class="photo" role="img" aria-label="Customers looking at televisions in a store" style="background:linear-gradient(135deg,#4a7fb8,#1e2f4a)"></div><h3>Lorem ipsum nipsum saye</h3><p class="meta">Posted on: Sep 29th, 2014</p><p class="excerpt">Lorem ipsum nipsum saye lorem ipsum nipsum saye. Lorem ipsum saye lorem ipsum nipsum saye.</p></article>
    </section>

    <section class="testimonials band">
      <h2 class="section-title">Customer Testimonials</h2>
      <span class="arrow arrow--prev" style="left:20px"></span>
      <div class="video" role="img" aria-label="Video testimonial from a customer" style="left:37px"><svg width="22" height="22" viewBox="0 0 22 22"><circle cx="11" cy="11" r="10" fill="#6dbb2f"/><path d="M8.5 6.5 L15.5 11 L8.5 15.5 Z" fill="#fff"/></svg></div>
      <div class="video" role="img" aria-label="Video testimonial from a customer" style="left:180px"><svg width="22" height="22" viewBox="0 0 22 22"><circle cx="11" cy="11" r="10" fill="#6dbb2f"/><path d="M8.5 6.5 L15.5 11 L8.5 15.5 Z" fill="#fff"/></svg></div>
      <div class="video" role="img" aria-label="Video testimonial from a customer" style="left:323px"><svg width="22" height="22" viewBox="0 0 22 22"><circle cx="11" cy="11" r="10" fill="#6dbb2f"/><path d="M8.5 6.5 L15.5 11 L8.5 15.5 Z" fill="#fff"/></svg></div>
      <span class="arrow arrow--next" style="left:471px"></span>
    </section>

    <section class="blog">
      <h2 class="section-title">Welcome to our Blog</h2>
      <article class="card" style="left:47px"><div class="photo" role="img" aria-label="Technician repairing electronics" style="background:linear-gradient(135deg,#8fa0b3,#2f3a4c)"></div><h3>Lorem ipsum nipsum saye</h3><p class="meta">Sep 29th, 2014 / 10 Comments</p></article>
      <article class="card" style="left:183px"><div class="photo" role="img" aria-label="Hands typing on a laptop keyboard" style="background:linear-gradient(135deg,#f1f3f2,#b8c0bd)"></div><h3>Lorem ipsum nipsum saye</h3><p class="meta">Sep 29th, 2014 / 10 Comments</p></article>
      <article class="card" style="left:320px"><div class="photo" role="img" aria-label="Woman holding a pen, thinking" style="background:linear-gradient(135deg,#d9eef2,#d8a57e)"></div><h3>Lorem ipsum nipsum saye</h3><p class="meta">Sep 29th, 2014 / 10 Comments</p></article>
    </section>

    <footer class="site-footer">
      <div class="foot-col" style="left:39px;width:97px"><h4>Welcome to BHA</h4><div class="foot-links"><ul><li>Our Plans</li><li>Benefits</li><li>About us</li><li>Contact us</li></ul><ul><li>Blog</li><li>News</li><li>Support</li><li>Terms</li></ul></div></div>
      <div class="foot-col" style="left:176px;width:128px"><h4>Social media feed</h4><div class="social-row"><i style="background:#3b5a9a"></i><i style="background:#3fa3d8"></i><i style="background:#c9302c"></i></div>
        <div class="feed"><div class="feed-item"><b></b><p><span>NAME OF PERSON</span>This is a sample post from our feed.</p></div><div class="feed-item"><b></b><p><span>NAME OF PERSON</span>This is a sample post from our feed.</p></div><div class="feed-item"><b></b><p><span>NAME OF PERSON</span>This is a sample post from our feed.</p></div></div></div>
      <div class="foot-col" style="left:343px;width:97px"><h4>Contact us</h4><ul class="contact-list"><li><svg width="6" height="7" viewBox="0 0 6 7"><path d="M3 0 C1.3 0 0 1.3 0 2.8 C0 4.6 3 7 3 7 C3 7 6 4.6 6 2.8 C6 1.3 4.7 0 3 0Z" fill="currentColor"/></svg><span>48 Lantern Way<br>Bayside 4209</span></li><li><svg width="6" height="6" viewBox="0 0 6 6"><rect width="6" height="6" rx="1" fill="currentColor"/></svg><span>Ph: (555) 010-4477</span></li><li><svg width="6" height="6" viewBox="0 0 6 6"><rect width="6" height="5" y=".5" fill="currentColor"/></svg><span>Email: care@brightharbor.example</span></li></ul></div>
    </footer>
    <div class="legal" style="position:absolute;left:0;width:500px;top:1130px">Copyright © 2014 Bright Harbor Assurance</div>
  </div>

  <!-- dark variant -->
  <div class="site site--dark">
    <header class="masthead">
      <div class="util-tab"><span>Login</span><span>Support</span><span>Call: 555-010-4477</span></div>
      <div class="brand"><span class="brand-mark"></span><span class="brand-name">Bright Harbor<br>Assurance</span></div>
      <nav class="nav"><span class="is-current">Home</span><span>Plans</span><span>Benefits</span><span>About us</span><span>Blog</span><span>News</span><span>Contact</span></nav>
    </header>

    <section class="hero">
      <div class="device" role="img" aria-label="Laptop showing the quote form and customer ratings screen"></div>
      <div class="claims"><span>Buys your device</span><span>Pay monthly to secure</span><span>Claim/fix your device</span></div>
      <div class="quote-btn">Get free quote</div>
      <div class="features">
        <div class="feature">
          <div class="feature-head"><svg width="18" height="18" viewBox="0 0 18 18"><circle cx="9" cy="9" r="8" fill="#fff"/><text x="9" y="12.5" font-size="10" text-anchor="middle" fill="#c8470f" font-family="Oswald,sans-serif">$</text></svg><span>Purchase in low<br>rates</span></div>
          <ul><li>- 1000 products available online</li><li>- Low as price as compare to market price</li><li>- Easy to purchase any product</li></ul>
        </div>
        <div class="feature">
          <div class="feature-head"><svg width="18" height="18" viewBox="0 0 18 18"><path d="M9 1 L16 4 V9 C16 13 12.5 16 9 17 C5.5 16 2 13 2 9 V4 Z" fill="#fff"/></svg><span>Protect devices<br>by paying monthly</span></div>
          <ul><li>- Pay montly fee</li><li>- Low rates as compare to others</li><li>- Secure your device in advance</li></ul>
        </div>
        <div class="feature">
          <div class="feature-head"><svg width="18" height="18" viewBox="0 0 18 18"><rect x="2" y="3" width="14" height="12" rx="2" fill="none" stroke="#fff" stroke-width="2"/></svg><span>Claim and fix<br>your device</span></div>
          <ul><li>- Claim your money you have paid</li><li>- Fix your broken devices</li><li>- Fast and reliable</li></ul>
        </div>
      </div>
    </section>

    <section class="ratings band">
      <h2 class="section-title">Customer Raiting</h2>
      <span class="arrow arrow--prev" style="left:11px"></span>
      <div class="store" style="left:29px"><span class="store-dot" style="background:#f2f2f2"></span><div><div class="store-name">Orchard Store</div><div class="store-note">some info came here<br>with description.</div><div class="stars" style="color:var(--star-red)">★★★★★</div></div></div>
      <div class="store" style="left:175px"><span class="store-dot" style="background:#f2f2f2"></span><div><div class="store-name">Riverbend Store</div><div class="store-note">some info came here<br>with description.</div><div class="stars" style="color:var(--star-blue)">★★★★★</div></div></div>
      <div class="store" style="left:326px"><span class="store-dot" style="background:#e0312a"></span><div><div class="store-name">Glimmer Store</div><div class="store-note">some info came here<br>with description.</div><div class="stars" style="color:var(--star-green)">★★★★★</div></div></div>
      <span class="arrow arrow--next" style="left:462px"></span>
    </section>

    <section class="news">
      <h2 class="section-title">Industry News</h2>
      <article class="card" style="left:47px"><div class="photo" role="img" aria-label="Shopper browsing laptops in an electronics store" style="background:linear-gradient(135deg,#c9d3dc,#3f5873)"></div><h3>Lorem ipsum nipsum saye</h3><p class="meta">Posted on: Sep 29th, 2014</p><p class="excerpt">Lorem ipsum nipsum saye lorem ipsum nipsum saye. Lorem ipsum saye lorem ipsum nipsum saye.</p></article>
      <article class="card" style="left:184px"><div class="photo" role="img" aria-label="Woman with a touchscreen interface" style="background:linear-gradient(135deg,#dfe6ea,#9aa7b0)"></div><h3>Lorem ipsum nipsum saye</h3><p class="meta">Posted on: Sep 29th, 2014</p><p class="excerpt">Lorem ipsum nipsum saye lorem ipsum nipsum saye. Lorem ipsum saye lorem ipsum nipsum saye.</p></article>
      <article class="card" style="left:320px"><div class="photo" role="img" aria-label="Customers looking at televisions in a store" style="background:linear-gradient(135deg,#4a7fb8,#1e2f4a)"></div><h3>Lorem ipsum nipsum saye</h3><p class="meta">Posted on: Sep 29th, 2014</p><p class="excerpt">Lorem ipsum nipsum saye lorem ipsum nipsum saye. Lorem ipsum saye lorem ipsum nipsum saye.</p></article>
    </section>

    <section class="testimonials band">
      <h2 class="section-title">Customer Testimonials</h2>
      <span class="arrow arrow--prev" style="left:20px"></span>
      <div class="video" role="img" aria-label="Video testimonial from a customer" style="left:37px"><svg width="22" height="22" viewBox="0 0 22 22"><circle cx="11" cy="11" r="10" fill="#6dbb2f"/><path d="M8.5 6.5 L15.5 11 L8.5 15.5 Z" fill="#fff"/></svg></div>
      <div class="video" role="img" aria-label="Video testimonial from a customer" style="left:180px"><svg width="22" height="22" viewBox="0 0 22 22"><circle cx="11" cy="11" r="10" fill="#6dbb2f"/><path d="M8.5 6.5 L15.5 11 L8.5 15.5 Z" fill="#fff"/></svg></div>
      <div class="video" role="img" aria-label="Video testimonial from a customer" style="left:323px"><svg width="22" height="22" viewBox="0 0 22 22"><circle cx="11" cy="11" r="10" fill="#6dbb2f"/><path d="M8.5 6.5 L15.5 11 L8.5 15.5 Z" fill="#fff"/></svg></div>
      <span class="arrow arrow--next" style="left:471px"></span>
    </section>

    <section class="blog">
      <h2 class="section-title">Welcome to our Blog</h2>
      <article class="card" style="left:47px"><div class="photo" role="img" aria-label="Technician repairing electronics" style="background:linear-gradient(135deg,#8fa0b3,#2f3a4c)"></div><h3>Lorem ipsum nipsum saye</h3><p class="meta">Sep 29th, 2014 / 10 Comments</p></article>
      <article class="card" style="left:183px"><div class="photo" role="img" aria-label="Hands typing on a laptop keyboard" style="background:linear-gradient(135deg,#f1f3f2,#b8c0bd)"></div><h3>Lorem ipsum nipsum saye</h3><p class="meta">Sep 29th, 2014 / 10 Comments</p></article>
      <article class="card" style="left:320px"><div class="photo" role="img" aria-label="Woman holding a pen, thinking" style="background:linear-gradient(135deg,#d9eef2,#d8a57e)"></div><h3>Lorem ipsum nipsum saye</h3><p class="meta">Sep 29th, 2014 / 10 Comments</p></article>
    </section>

    <footer class="site-footer">
      <div class="foot-col" style="left:39px;width:97px"><h4>Welcome to BHA</h4><div class="foot-links"><ul><li>Our Plans</li><li>Benefits</li><li>About us</li><li>Contact us</li></ul><ul><li>Blog</li><li>News</li><li>Support</li><li>Terms</li></ul></div></div>
      <div class="foot-col" style="left:176px;width:128px"><h4>Social media feed</h4><div class="social-row"><i style="background:#3b5a9a"></i><i style="background:#3fa3d8"></i><i style="background:#c9302c"></i></div>
        <div class="feed"><div class="feed-item"><b></b><p><span>NAME OF PERSON</span>This is a sample post from our feed.</p></div><div class="feed-item"><b></b><p><span>NAME OF PERSON</span>This is a sample post from our feed.</p></div><div class="feed-item"><b></b><p><span>NAME OF PERSON</span>This is a sample post from our feed.</p></div></div></div>
      <div class="foot-col" style="left:343px;width:97px"><h4>Contact us</h4><ul class="contact-list"><li><svg width="6" height="7" viewBox="0 0 6 7"><path d="M3 0 C1.3 0 0 1.3 0 2.8 C0 4.6 3 7 3 7 C3 7 6 4.6 6 2.8 C6 1.3 4.7 0 3 0Z" fill="currentColor"/></svg><span>48 Lantern Way<br>Bayside 4209</span></li><li><svg width="6" height="6" viewBox="0 0 6 6"><rect width="6" height="6" rx="1" fill="currentColor"/></svg><span>Ph: (555) 010-4477</span></li><li><svg width="6" height="6" viewBox="0 0 6 6"><rect width="6" height="5" y=".5" fill="currentColor"/></svg><span>Email: care@brightharbor.example</span></li></ul></div>
    </footer>
    <div class="legal" style="position:absolute;left:0;width:500px;top:1130px">Copyright © 2014 Bright Harbor Assurance</div>
  </div>

</div>
</body>
</html>
```